Brindovalle Business cards

Dear team, I need to get the design file to suit it to our team. The focus of the business card is the Automotive Market and the design must be in black colour and the logo must be in glossy black. On the front of the card I need to get the following info:

- Name and Surname
- Title
- eMail
- Phone Number
- Skype account
- domain address

```html
<!DOCTYPE html>
<html lang="en">
<head>
<meta charset="utf-8">
<title>Brindovalle Business Card</title>
<link rel="stylesheet" href="https://fonts.googleapis.com/css2?family=Oswald:wght@600&family=Open+Sans:wght@400;700&display=swap">
<style>
  :root {
    --stage: #2b2b2d;
    --card-black: #1b1b1d;
    --brand-red: #ee2b33;
    --white: #ffffff;
  }
  * { margin: 0; padding: 0; box-sizing: border-box; }
  html, body { width: 1200px; height: 900px; overflow: hidden; background: var(--stage); }
  .card {
    position: absolute; left: 100px; top: 164px;
    width: 1000px; height: 572px;
    background: var(--card-black);
    border-radius: 34px; overflow: hidden;
    font-family: "Open Sans", Arial, sans-serif; color: var(--white);
  }
  .card-swoosh { position: absolute; inset: 0; }
  .brand {
    position: absolute; left: 340px; top: 64px;
    display: flex; align-items: center; gap: 20px;
    white-space: nowrap;
  }
  .brand-dot { width: 54px; height: 54px; border-radius: 50%; background: var(--brand-red); flex: none; }
  .brand-name { font-weight: 700; font-size: 58px; letter-spacing: -1px; color: var(--white); }
  .holder { position: absolute; left: 100px; top: 196px; width: 340px; text-align: right; }
  .holder-name {
    font-family: "Oswald", "Arial Narrow", sans-serif; font-weight: 600;
    font-size: 50px; line-height: 1; color: var(--brand-red);
    text-transform: uppercase; white-space: nowrap;
    transform: skewX(-8deg);
  }
  .holder-title { font-size: 24px; line-height: 1; margin-top: 10px; }
  .divider { position: absolute; left: 466px; top: 200px; width: 4px; height: 104px; background: var(--brand-red); }
  .contacts { position: absolute; left: 494px; top: 200px; list-style: none; font-size: 24px; line-height: 35px; white-space: nowrap; }
  .contacts li { display: flex; align-items: center; gap: 10px; }
  .contacts svg { width: 20px; height: 20px; flex: none; }
  .address {
    position: absolute; left: 90px; top: 396px;
    font-size: 24px; white-space: nowrap;
    transform: rotate(10deg); transform-origin: left center;
  }
</style>
</head>
<body>
  <div class="card">
    <svg class="card-swoosh" viewBox="0 0 1000 572" aria-hidden="true">
      <path d="M0,312 C250,322 600,452 1000,492 L1000,572 L0,572 Z" fill="var(--brand-red)"/>
      <path d="M0,290 C250,300 600,430 1000,470 L1000,480 C600,440 250,310 0,300 Z" fill="var(--white)"/>
    </svg>

    <div class="brand">
      <span class="brand-dot"></span>
      <span class="brand-name">Brindovalle.com</span>
    </div>

    <div class="holder">
      <p class="holder-name">Marco Venturi</p>
      <p class="holder-title">Director</p>
    </div>

    <span class="divider"></span>

    <ul class="contacts">
      <li>
        <svg viewBox="0 0 20 20"><path d="M5 2 L8 6 L6 8 C7 11 9 13 12 14 L14 12 L18 15 L16 18 C9 18 2 11 2 4 Z" fill="var(--brand-red)"/></svg>
        918-555-0172
      </li>
      <li>
        <svg viewBox="0 0 20 20"><rect x="1" y="4" width="18" height="12" fill="var(--brand-red)"/><path d="M1 4 L10 11 L19 4" fill="none" stroke="var(--card-black)" stroke-width="1.5"/></svg>
        info@brindovalle.com
      </li>
      <li>
        <svg viewBox="0 0 20 20"><circle cx="10" cy="10" r="9" fill="var(--brand-red)"/></svg>
        brindovalle
      </li>
    </ul>

    <p class="address">2240 W Calder, Tulsa, Oklahoma 74107</p>
  </div>
</body>
</html>
```